Website design for legal tech start up in Switzerland (B2B)

We are for a legal tech start up in Switzerland called KOVA. We have been running since August 2016. This will be our first live website.

We need a website designed and business card design for our start-up in Switzerland. We also need the Web design to be converted into HTML and CSS files.

Function of website:
• To inform potential customers of our services
• Form a key part of our digital marketing and sales footprint.
• Branding

Please find attached logo.
Updates

Project Deadline Extended Reason: Giving us time to review submissions and provide opportunity for more submissions. Added Thursday, February 16, 2017

Project Deadline Extended
Reason: Looking for more idea's not necessarily set on blue and grey colours only.

Target Market(s)

B2B tech powered legal services.

Industry/Entity Type

Legal

Contact Information for Business Card

Lean and slick design.

Coding

Coded - Design and coding required

Number of Pages Required

5+ page

Requirements
Must have
• VERY LEAN AND CLEAN DESIGN!
• We have received many great standard designs, but we are looking for something more out-of-the box: You can get inspiration from these designs: http://www.pixelvane.com/websites/clean/
• Thanks!!
• Easy content management system
• Well structured coding for additional development
• Responsive webpage for all types of devices
• SEO optimized
• Tabs (Home, services, team, careers, blog, contact us)
• Colour scheme complementary to logo
Nice to have
• Look and Design - Approachable, High-tech, Modern
• Easy to add chat bot capability in future
Should not have
• Too busy/ too much clutter
• Not take to long to load

```html
<!DOCTYPE html>
<html lang="en">
<head>
<meta charset="utf-8">
<title>KOVA — Legal Services</title>
<link href="https://fonts.googleapis.com/css2?family=Lato:wght@400;700;900&family=Open+Sans:wght@400;600&display=swap" rel="stylesheet">
<style>
:root{
  --navy:#1b3a6b;
  --navy-dark:#2a3550;
  --ink:#1e1e1e;
  --muted:#555;
  --grey-bg:#efefef;
  --line:#cfcfcf;
  --white:#fff;
  --fb:#3b5998;--tw:#55acee;--li:#0e76a8;--ig:#e4405f;
}
*{box-sizing:border-box;margin:0;padding:0}
html,body{width:1200px;height:3303px;overflow:hidden}
body{font-family:"Open Sans",sans-serif;color:var(--ink);background:var(--white);position:relative}
section,header,footer{position:absolute;left:0;width:1200px}
.abs{position:absolute}
h1,h2,h3{font-family:"Lato",sans-serif}
.btn{position:absolute;display:flex;align-items:center;justify-content:center;font-family:"Open Sans",sans-serif;font-size:14px;font-weight:600;border-radius:2px}
.btn-solid{background:var(--navy);color:var(--white)}
.btn-outline{border:2px solid #444;color:var(--ink);background:var(--white)}

/* header */
.site-header{top:0;height:128px;border-top:4px solid var(--navy)}
.brand{left:99px;top:40px;font-family:"Lato",sans-serif;font-weight:700;font-size:48px;letter-spacing:2px;color:var(--navy-dark);line-height:1}
.top-contact{top:18px;right:99px;display:flex;gap:24px;font-size:17px;align-items:center}
.top-contact span{display:flex;align-items:center;gap:10px}
.top-contact i{width:30px;height:30px;border-radius:50%;background:var(--navy-dark);display:inline-flex;align-items:center;justify-content:center}
.nav{top:80px;right:99px;display:flex;align-items:center;gap:30px;font-family:"Lato",sans-serif;font-weight:700;font-size:14px;letter-spacing:.5px}
.nav a{color:var(--ink);text-decoration:none;padding:6px 9px}
.nav a.active{border:2px solid var(--navy);color:var(--navy)}
.nav .search{width:32px;height:32px;border:2px solid #333;border-radius:50%;display:flex;align-items:center;justify-content:center}

/* hero */
.hero{top:128px;height:513px;background:linear-gradient(135deg,#2f3a57,#262f48)}
.hero-photo{left:595px;top:0;width:605px;height:513px;background:linear-gradient(160deg,#5b5f66,#c9c3b6 45%,#3b3e45)}
.hero h1{left:99px;top:105px;color:var(--white);font-size:44px;font-weight:700;letter-spacing:.5px}
.hero p{left:99px;top:190px;width:470px;color:#e6e8ef;font-size:16px;line-height:29px}
.hero .btn{left:99px;top:282px;width:126px;height:46px;border:2px solid var(--white);color:var(--white);font-size:14px;background:none}
.dots{left:99px;top:370px;display:flex;gap:5px}
.dots b{width:13px;height:13px;border-radius:50%;border:2px solid var(--white)}
.dots b:first-child{background:var(--white)}
.hero-arrow{left:530px;top:80px}

/* about */
.about{top:641px;height:396px}
.about h2{left:99px;top:55px;font-size:30px;color:var(--navy);font-weight:700}
.about p{left:99px;width:610px;font-size:13.5px;line-height:21px;color:#333}
.about .p1{top:125px}.about .p2{top:212px}
.about .btn{left:99px;top:284px;width:123px;height:46px}
.about-photo{left:727px;top:0;width:473px;height:396px;background:linear-gradient(110deg,#f4f4f4 10%,#9a9593 55%,#3e3a38)}

/* services */
.services{top:1037px;height:586px;background:var(--grey-bg)}
.sec-title{width:1200px;text-align:center;font-size:28px;font-weight:700;color:var(--navy)}
.sec-sub{left:200px;width:800px;text-align:center;font-size:13.5px;line-height:26px;color:#555}
.underline{left:551px;width:98px;height:2px;background:var(--navy)}
.services .sec-title{top:48px}
.services .sec-sub{top:98px}
.connector{left:282px;top:276px}
.service{top:196px;width:260px;text-align:center}
.service .ring{width:164px;height:164px;margin:0 auto;border:3px solid var(--navy);border-radius:50%;display:flex;align-items:center;justify-content:center;background:var(--white)}
.service.featured .ring{background:var(--navy);box-shadow:inset 0 0 0 8px var(--white);}
.service h3{margin-top:26px;font-family:"Open Sans",sans-serif;font-weight:600;font-size:18px;color:var(--ink)}
.service.featured h3{color:var(--navy)}
.service p{margin:12px auto 0;width:210px;font-size:12.5px;line-height:23px;color:#444}
.service .btn{position:relative;margin:22px auto 0;width:110px;height:40px;border-radius:20px;font-size:13px}
.service.featured .btn{background:var(--navy);color:var(--white);border-color:var(--navy)}

/* team */
.team{top:1623px;height:557px}
.team .sec-title{top:60px}
.team .underline{top:108px}
.member{top:163px;width:240px;text-align:center}
.member .photo{width:240px;height:202px;background:linear-gradient(180deg,#cfcfcf,#8f8f8f)}
.member h3{margin-top:20px;font-family:"Open Sans",sans-serif;font-weight:600;font-size:16px}
.member .role{margin-top:10px;font-size:15px;color:var(--navy)}
.social{margin-top:14px;display:flex;justify-content:center;gap:7px}
.social i{width:24px;height:24px;border-radius:50%}
.s1{background:var(--fb)}.s2{background:var(--tw)}.s3{background:var(--li)}.s4{background:var(--ig)}

/* blog */
.blog{top:2180px;height:654px;background:var(--grey-bg)}
.blog .sec-title{top:52px}
.blog .underline{top:102px}
.post{top:152px;width:317px;text-align:center}
.post .photo{position:relative;width:317px;height:227px}
.post .date{position:absolute;left:0;bottom:0;width:58px;height:64px;background:#2d2d2d;color:var(--white);font-weight:600;font-size:15px;line-height:22px;padding-top:10px}
.post .date em{display:block;font-style:normal;background:var(--navy);height:32px;line-height:32px;margin-top:4px}
.post h3{margin-top:38px;font-family:"Open Sans",sans-serif;font-weight:600;font-size:17px}
.post p{margin:14px auto 0;width:270px;font-size:12.5px;line-height:20px;color:#444}
.post .btn{position:relative;margin:20px auto 0;width:121px;height:42px}

/* contact */
.contact{top:2834px;height:469px;border-top:3px solid var(--navy)}
.contact h2{left:99px;top:50px;font-size:28px;color:var(--navy)}
.contact .ul{left:99px;top:94px;width:88px;height:2px;background:var(--navy)}
.c-row{left:99px;display:flex;align-items:center;gap:22px;font-size:16px;line-height:28px}
.c-row i{width:48px;height:48px;border-radius:50%;background:var(--navy);display:flex;align-items:center;justify-content:center;flex:none}
.form-lead{left:484px;top:52px;font-size:17px}
.field{position:absolute;border:2px solid #555;height:40px;font-size:13px;color:#888;padding:10px}
.contact .btn{left:484px;top:312px;width:115px;height:40px}
.divider{left:99px;top:391px;width:1002px;height:1px;background:var(--line)}
.copy{left:0;top:426px;width:1200px;text-align:center;font-size:14px}
</style>
</head>
<body>

<header class="site-header">
  <div class="abs brand">KOVA</div>
  <div class="abs top-contact">
    <span><i><svg width="14" height="11" viewBox="0 0 14 11"><rect x="1" y="1" width="12" height="9" fill="none" stroke="#fff" stroke-width="1.5"/><path d="M1 1l6 5 6-5" fill="none" stroke="#fff" stroke-width="1.5"/></svg></i>info@kova.in</span>
    <span><i><svg width="14" height="14" viewBox="0 0 24 24"><path fill="#fff" d="M6.6 10.8a15 15 0 006.6 6.6l2.2-2.2c.3-.3.7-.4 1-.2 1.1.4 2.3.6 3.6.6.6 0 1 .4 1 1V20c0 .6-.4 1-1 1A17 17 0 013 4c0-.6.4-1 1-1h3.5c.6 0 1 .4 1 1 0 1.3.2 2.5.6 3.6.1.3 0 .7-.2 1z"/></svg></i><b>180 555 0147</b></span>
  </div>
  <nav class="abs nav">
    <a class="active">HOME</a><a>SERVICES</a><a>TEAM</a><a>CAREERS</a><a>BLOG</a><a>CONTACT US</a>
    <span class="search"><svg width="14" height="14" viewBox="0 0 14 14"><circle cx="6" cy="6" r="4.5" fill="none" stroke="#333" stroke-width="1.8"/><path d="M9.5 9.5L13 13" stroke="#333" stroke-width="1.8"/></svg></span>
  </nav>
</header>

<section class="hero">
  <div class="abs hero-photo" role="img" aria-label="Overhead photo of a business team meeting around a table with laptops and papers"></div>
  <svg class="abs hero-arrow" width="150" height="70" viewBox="0 0 150 70"><path d="M5 40 C40 5 100 5 135 45" fill="none" stroke="#fff" stroke-width="4" stroke-linecap="round"/><path d="M118 42 L137 48 L138 28" fill="none" stroke="#fff" stroke-width="4" stroke-linecap="round" stroke-linejoin="round"/></svg>
  <h1 class="abs">WELCOME TO KOVA</h1>
  <p class="abs">Nemo enim ipsam voluptatem quia voluptas sit aspernatur aut odit aut fugit, sed quia consequntur.</p>
  <a class="btn">CONTACT US</a>
  <div class="abs dots"><b></b><b></b><b></b><b></b><b></b></div>
</section>

<section class="about">
  <h2 class="abs">About KOVA</h2>
  <p class="abs p1">Nemo enim ipsam voluptatem quia voluptas sit aspernatur aut odit aut fugit, sed quia consequuntur magni dolores eos qui ratione voluptatem sequi nesciunt. Neque porro quisquam est, qui dolorem ipsum quia dolor sit amet, consectetur, adipisci velit, sed quia non numquam.</p>
  <p class="abs p2">Sed ut perspiciatis unde omnis iste natus error sit voluptatem accusantium doloremque laudantium, totam rem aperiam, eaque ipsa quae ab illo inventore veritatis.</p>
  <a class="btn btn-solid">Read More</a>
  <div class="abs about-photo" role="img" aria-label="Photo of a person in a suit holding a clipboard"></div>
</section>

<section class="services">
  <h2 class="abs sec-title">Our Services</h2>
  <p class="abs sec-sub">Nemo enim ipsam voluptatem quia voluptas sit aspernatur aut odit aut fugit, sed quia consequuntur magni dolores eos qui ratione voluptatem.</p>
  <svg class="abs connector" width="640" height="12" viewBox="0 0 640 12">
    <g stroke="#1b3a6b" stroke-width="1.5" stroke-dasharray="5 4" fill="none"><path d="M0 6H640"/></g>
    <g fill="#fff" stroke="#1b3a6b" stroke-width="2"><circle cx="50" cy="6" r="6"/><circle cx="318" cy="6" r="6"/><circle cx="586" cy="6" r="6"/></g>
    <circle cx="318" cy="6" r="2.5" fill="#1b3a6b"/>
  </svg>
  <div class="abs service" style="left:70px">
    <div class="ring"><svg width="70" height="70" viewBox="0 0 70 70" fill="#1b3a6b"><path d="M35 4a10 10 0 0110 10c0 8-10 18-10 18S25 22 25 14A10 10 0 0135 4z"/><text x="35" y="18" font-size="12" font-family="Lato" font-weight="700" fill="#fff" text-anchor="middle">$</text><path d="M6 48l14-11 14 11v16H6z"/><path d="M36 48l14-11 14 11v16H36z"/><rect x="16" y="54" width="7" height="10" fill="#fff"/><rect x="46" y="54" width="7" height="10" fill="#fff"/></svg></div>
    <h3>Probate Law</h3>
    <p>Nemo enim ipsam voluptatem quia voluptas sit aspernatur aut odit aut fugit, sed quia consequuntur.</p>
    <a class="btn btn-outline">Learn More</a>
  </div>
  <div class="abs service featured" style="left:337px">
    <div class="ring"><svg width="70" height="70" viewBox="0 0 70 70" fill="#fff"><circle cx="22" cy="12" r="6"/><path d="M14 22h16v26h-4v18h-8V48h-4z"/><path d="M44 12v50M34 62h20" stroke="#fff" stroke-width="3"/><path d="M32 24h26" stroke="#fff" stroke-width="2"/><path d="M30 38a5 4 0 0010 0l-5-12zM50 38a5 4 0 0010 0l-5-12z"/></svg></div>
    <h3>Business Law</h3>
    <p>Nemo enim ipsam voluptatem quia voluptas sit aspernatur aut odit aut fugit, sed quia consequuntur.</p>
    <a class="btn btn-outline">Learn More</a>
  </div>
  <div class="abs service" style="left:603px">
    <div class="ring"><svg width="70" height="70" viewBox="0 0 70 70" fill="none" stroke="#1b3a6b" stroke-width="3"><rect x="8" y="12" width="54" height="36" rx="2"/><path d="M2 54h66l-4 6H6z" fill="#1b3a6b"/><path d="M22 36l13-11 13 11M26 33v10h18V33"/></svg></div>
    <h3>Injury Law</h3>
    <p>Nemo enim ipsam voluptatem quia voluptas sit aspernatur aut odit aut fugit, sed quia consequuntur.</p>
    <a class="btn btn-outline">Learn More</a>
  </div>
  <div class="abs service" style="left:872px">
    <div class="ring"><svg width="70" height="70" viewBox="0 0 70 70" fill="#1b3a6b"><circle cx="35" cy="12" r="6"/><path d="M24 22h22v6H24z"/><rect x="18" y="30" width="34" height="8"/><rect x="22" y="38" width="26" height="20"/><rect x="16" y="58" width="38" height="6"/><rect x="29" y="43" width="12" height="10" fill="#fff"/></svg></div>
    <h3>Special Needs Planning</h3>
    <p>Nemo enim ipsam voluptatem quia voluptas sit aspernatur aut odit aut fugit, sed quia consequuntur.</p>
    <a class="btn btn-outline">Learn More</a>
  </div>
</section>

<section class="team">
  <h2 class="abs sec-title">Our Team Members</h2>
  <div class="abs underline"></div>
  <div class="abs member" style="left:106px">
    <div class="photo" role="img" aria-label="Portrait photo of a team member"></div>
    <h3>JONAS FERRELI</h3><div class="role">KOVA Member</div>
    <div class="social"><i class="s1"></i><i class="s2"></i><i class="s3"></i><i class="s4"></i></div>
  </div>
  <div class="abs member" style="left:356px">
    <div class="photo" role="img" aria-label="Portrait photo of a team member"></div>
    <h3>BRENNAN</h3><div class="role">KOVA Manager</div>
    <div class="social"><i class="s1"></i><i class="s2"></i><i class="s3"></i><i class="s4"></i></div>
  </div>
  <div class="abs member" style="left:605px">
    <div class="photo" role="img" aria-label="Portrait photo of a team member"></div>
    <h3>WHITAKER</h3><div class="role">KOVA CEO</div>
    <div class="social"><i class="s1"></i><i class="s2"></i><i class="s3"></i><i class="s4"></i></div>
  </div>
  <div class="abs member" style="left:854px">
    <div class="photo" role="img" aria-label="Portrait photo of a team member"></div>
    <h3>LANGFORD</h3><div class="role">KOVA Member</div>
    <div class="social"><i class="s1"></i><i class="s2"></i><i class="s3"></i><i class="s4"></i></div>
  </div>
</section>

<section class="blog">
  <h2 class="abs sec-title">Our Blog Posts</h2>
  <div class="abs underline"></div>
  <article class="abs post" style="left:99px">
    <div class="photo" role="img" aria-label="Photo of colleagues reviewing documents at a desk" style="background:linear-gradient(135deg,#6d8fae,#d8d0c8 60%,#8a6f66)"><div class="date">JAN<em>17</em></div></div>
    <h3>Nemo enim ipsam</h3>
    <p>Sed ut perspiciatis unde omnis iste natus error sit voluptatem accusantium doloremque laudantium, totam rem aperiam.</p>
    <a class="btn btn-solid">Read More</a>
  </article>
  <article class="abs post" style="left:442px">
    <div class="photo" role="img" aria-label="Photo of a businesswoman standing in front of her team" style="background:linear-gradient(135deg,#3a3a3c,#c7c7cb 55%,#2a2a2c)"><div class="date">DEC<em>21</em></div></div>
    <h3>Voluptatem quia voluptas</h3>
    <p>Sed ut perspiciatis unde omnis iste natus error sit voluptatem accusantium doloremque laudantium, totam rem aperiam.</p>
    <a class="btn btn-outline">Read More</a>
  </article>
  <article class="abs post" style="left:784px">
    <div class="photo" role="img" aria-label="Photo of hands signing a contract with a pen" style="background:linear-gradient(135deg,#e6e6e6,#b9b4ae 55%,#7a7470)"><div class="date">DEC<em>14</em></div></div>
    <h3>Aspernatur aut odit fugit</h3>
    <p>Sed ut perspiciatis unde omnis iste natus error sit voluptatem accusantium doloremque laudantium, totam rem aperiam.</p>
    <a class="btn btn-outline">Read More</a>
  </article>
</section>

<footer class="contact">
  <h2 class="abs">Contact Us</h2>
  <div class="abs ul"></div>
  <div class="abs c-row" style="top:137px"><i><svg width="18" height="14" viewBox="0 0 14 11"><rect x="1" y="1" width="12" height="9" fill="none" stroke="#fff" stroke-width="1.4"/><path d="M1 1l6 5 6-5" fill="none" stroke="#fff" stroke-width="1.4"/></svg></i>info@kova.com</div>
  <div class="abs c-row" style="top:202px"><i><svg width="16" height="20" viewBox="0 0 16 20"><path d="M8 1a6 6 0 016 6c0 5-6 12-6 12S2 12 2 7a6 6 0 016-6z" fill="none" stroke="#fff" stroke-width="1.6"/><circle cx="8" cy="7" r="2" fill="#fff"/></svg></i>48 Harbor Lane<br>Linden, MD 1234</div>
  <div class="abs c-row" style="top:291px"><i style="background:#fff;border:2px solid var(--navy)"><svg width="18" height="18" viewBox="0 0 24 24"><path fill="#1b3a6b" d="M6.6 10.8a15 15 0 006.6 6.6l2.2-2.2c.3-.3.7-.4 1-.2 1.1.4 2.3.6 3.6.6.6 0 1 .4 1 1V20c0 .6-.4 1-1 1A17 17 0 013 4c0-.6.4-1 1-1h3.5c.6 0 1 .4 1 1 0 1.3.2 2.5.6 3.6.1.3 0 .7-.2 1z"/></svg></i>180 555 0147</div>

  <p class="abs form-lead">Fill out the form below, and we'll contact you shortly.</p>
  <div class="field" style="left:484px;top:100px;width:291px">First Name</div>
  <div class="field" style="left:809px;top:100px;width:292px">Last Name</div>
  <div class="field" style="left:484px;top:154px;width:291px">Phone Number</div>
  <div class="field" style="left:809px;top:154px;width:292px">E-Mail Address</div>
  <div class="field" style="left:484px;top:210px;width:617px;height:84px">Message</div>
  <a class="btn btn-solid">Send Now</a>
  <div class="abs divider"></div>
  <p class="abs copy">2017 © KOVA. All rights reserved.</p>
</footer>

</body>
</html>
```